Retail/Wholesale website graphic template

I need to design a new graphic template for a website for a client. The website will be a retail/wholesale company site with most pages dedicated to presentation. There will also be an online store and a blog. However, you don't need to worry about those. All I need from you is a graphic template for a generic site page.

It will need to include standard UI elements, in case I need those. I am attaching a more detailed assignment in .docx format.

The logo is also attached.

Target Market(s)

small business owners, (occasional) retail customers

Industry/Entity Type

Wholesale

Number of Pages Required

1 page

Font styles to use
Serif
Sans Serif

Colors
ec1f27
474747

Requirements
Must have
• must match logo, be clean, minimal and with slightly larger text size
Should not have
• must not be modern-looking where you have to scroll and scroll and scroll to get to the bottom of the homepage. most of my visitors are "old" people, they do not get this type of design.

```html
<!DOCTYPE html>
<html lang="en">
<head>
<meta charset="utf-8">
<title>Harbor Crate Imports</title>
<link href="https://fonts.googleapis.com/css2?family=Mulish:wght@400;600;700;800&family=Open+Sans:wght@400;600;700&display=swap" rel="stylesheet">
<style>
:root{
  --red:#ec1f27;
  --ink:#474747;
  --dark:#1c1b1c;
  --text:#5a5a5a;
  --band:#ececec;
  --white:#ffffff;
  --foot-text:#e2e2e2;
}
*{box-sizing:border-box;margin:0;padding:0}
html,body{width:1200px;height:3974px;overflow:hidden}
body{position:relative;background:var(--white);font-family:"Open Sans",Arial,sans-serif;color:var(--text)}
.abs{position:absolute}
.btn{position:absolute;background:var(--red);color:var(--white);font:700 15px "Open Sans",sans-serif;border-radius:24px;text-align:center;text-transform:uppercase;white-space:nowrap}
.section-title{position:absolute;font:600 40px "Mulish",sans-serif;color:#222}
.section-title::after{content:"";position:absolute;left:0;bottom:-16px;width:70px;height:3px;background:var(--red)}
.section-title.center{left:0;width:1200px;text-align:center}
.section-title.center::after{left:565px}

/* top bar */
.topbar{left:0;top:0;width:1200px;height:37px;background:var(--red);color:var(--white);font-size:14px}
.topbar span{position:absolute;top:9px;display:flex;align-items:center;gap:8px}
/* nav */
.nav{left:0;top:37px;width:1200px;height:85px;background:var(--white)}
.brand{position:absolute;left:100px;top:22px;font:800 26px "Mulish",sans-serif;color:var(--ink);letter-spacing:1px}
.menu{position:absolute;right:100px;top:32px;display:flex;gap:30px;font:600 15px "Open Sans",sans-serif;color:#222}
/* hero */
.hero-photo{left:0;top:122px;width:1200px;height:561px;background:linear-gradient(120deg,#6b625d,#3e3836 45%,#5c4b40 80%,#2e2a28)}
.hero-shade{left:0;top:122px;width:1200px;height:561px;background:rgba(0,0,0,.35)}
.hero-title{left:0;top:218px;width:1200px;text-align:center;font:800 66px "Mulish",sans-serif;color:var(--white);white-space:nowrap}
.hero-sub{left:280px;top:302px;width:640px;text-align:center;font:600 22px/34px "Open Sans",sans-serif;color:var(--white)}
.slide{position:absolute;box-shadow:0 10px 30px rgba(0,0,0,.3)}
.arrow{position:absolute;top:738px}
/* about */
.about-text{left:100px;top:1124px;width:470px;font-size:14.5px;line-height:28px}
.dots{left:1095px;top:1380px;display:flex;gap:5px}
.dots i{width:13px;height:13px;border-radius:50%;border:2px solid var(--red)}
/* services */
.band{left:0;width:1200px;background:var(--band)}
.card{position:absolute;top:1725px;width:244px;height:250px;background:var(--white);text-align:center}
.card svg{margin-top:28px}
.card h3{font:700 17px "Open Sans",sans-serif;color:#222;margin-top:18px;white-space:nowrap}
.card p{font-size:14px;line-height:26px;margin-top:8px}
.card .btn{position:absolute;left:60px;top:210px;width:124px;height:38px;line-height:38px;font-size:13px}
/* what we do */
.wwd-list{left:702px;top:2302px}
.wwd-list h4{font:600 18px "Open Sans",sans-serif;color:#222;margin-bottom:17px}
.wwd-list li{list-style:none;font-size:15px;height:31px;position:relative;padding-left:26px}
.wwd-list li::before{content:"";position:absolute;left:0;top:7px;width:7px;height:7px;border-radius:50%;background:var(--red)}
/* blog */
.post{position:absolute;top:2910px;width:308px;height:403px;background:var(--white);box-shadow:0 4px 14px rgba(0,0,0,.15)}
.post .ph{height:209px}
.post p{margin:24px 26px 0;font-size:14.5px;line-height:27px}
.post .author{position:absolute;left:20px;right:20px;top:292px;display:flex;align-items:center;gap:12px;font:700 14px "Open Sans",sans-serif;color:#222;white-space:nowrap}
.post .author i{flex:none;width:44px;height:44px;border-radius:50%;background:#9a8f88}
.post .author::after{content:"";flex:1;height:1px;background:#ddd}
.post .btn{left:170px;top:349px;width:118px;height:38px;line-height:38px;text-transform:none;font-size:14px}
/* footer */
.footer{left:0;top:3427px;width:1200px;height:498px;background:var(--dark)}
.foot-brand{left:0;top:3496px;width:1200px;text-align:center;font:800 32px "Mulish",sans-serif;color:var(--white);letter-spacing:2px}
.social{left:478px;top:3576px;display:flex;gap:13px}
.social i{width:40px;height:40px;border-radius:50%;border:1.5px solid var(--red)}
.fcol{top:3706px;color:var(--foot-text)}
.fcol h5{font:400 22px "Mulish",sans-serif;color:var(--white);position:relative;margin-bottom:38px}
.fcol h5::after{content:"";position:absolute;left:0;bottom:-12px;width:42px;height:2px;background:var(--red)}
.fcol ul{list-style:none;font-size:13.5px;line-height:26px}
.contact li{display:flex;gap:14px;align-items:flex-start}
.bottombar{left:0;top:3925px;width:1200px;height:49px;background:var(--red);color:var(--white);font-size:13px;text-align:center;line-height:49px}
</style>
</head>
<body>

<div class="abs topbar">
  <span style="left:100px"><svg width="14" height="14" viewBox="0 0 24 24" fill="#fff"><path d="M6.6 10.8a15 15 0 006.6 6.6l2.2-2.2c.3-.3.7-.4 1-.2 1.1.4 2.3.6 3.6.6.6 0 1 .4 1 1V20c0 .6-.4 1-1 1A17 17 0 013 4c0-.6.4-1 1-1h3.5c.6 0 1 .4 1 1 0 1.2.2 2.4.6 3.6.1.3 0 .7-.2 1z"/></svg>+1-111-111-111</span>
  <span style="left:260px"><svg width="16" height="12" viewBox="0 0 24 18" fill="#fff"><path d="M0 0h24v18H0z"/><path d="M2 2l10 8 10-8" stroke="#ec1f27" stroke-width="2" fill="none"/></svg><u>info@harborcrate.com</u></span>
  <span style="right:100px"><svg width="12" height="14" viewBox="0 0 12 14" fill="#fff"><rect x="0" y="6" width="12" height="8" rx="1"/><path d="M3 6V4a3 3 0 016 0v2" stroke="#fff" stroke-width="2" fill="none"/></svg>LOG IN</span>
</div>

<div class="abs nav">
  <div class="brand">HARBOR CRATE</div>
  <div class="menu"><span>Home</span><span>About Us</span><span>Services</span><span>What We Do</span><span>Blog</span><span>Contact Us</span>
    <svg width="16" height="16" viewBox="0 0 24 24" fill="none" stroke="#222" stroke-width="3"><circle cx="10" cy="10" r="7"/><path d="M15 15l7 7"/></svg></div>
</div>

<div class="abs hero-photo" role="img" aria-label="Shoppers browsing clothing racks in a store"></div>
<div class="abs hero-shade"></div>
<h1 class="abs hero-title">HARBOR CRATE IMPORTS</h1>
<p class="abs hero-sub">Lorem ipsum dolor sit amet, consectetur adipiscing<br>elit, sed do eiusmod tempor incididunt ut</p>
<div class="btn" style="left:521px;top:384px;width:158px;height:44px;line-height:44px">Read More</div>

<div class="slide" style="left:300px;top:545px;width:600px;height:265px;background:#b9b3ad" role="img" aria-label="Warehouse photos behind the main slide"></div>
<div class="slide" style="left:352px;top:500px;width:496px;height:335px;background:#a59a8e" role="img" aria-label="Shipping yard photo"></div>
<div class="slide" style="left:403px;top:450px;width:392px;height:450px;background:linear-gradient(180deg,#86b6e0 0%,#b9d4ea 30%,#9a5a42 31%,#7c3d2f 70%,#6a6a6a 100%)" role="img" aria-label="Stacked shipping containers against blue sky"></div>
<svg class="arrow" style="left:176px" width="30" height="64" viewBox="0 0 30 64"><path d="M26 2L4 32l22 30" stroke="#222" stroke-width="3" fill="none"/></svg>
<svg class="arrow" style="left:992px" width="30" height="64" viewBox="0 0 30 64"><path d="M4 2l22 30L4 62" stroke="#222" stroke-width="3" fill="none"/></svg>

<h2 class="section-title" style="left:100px;top:1026px">About Us</h2>
<p class="abs about-text">At vero eos et accusamus et iusto odio dignissimos ducimus qui blanditiis praesentium voluptatum deleniti atque corrupti quos dolores et quas tias excepturi sint occaecati cupiditate non provident, similique sunt in culpa qui officia deserunt mollitia animi, id est laborum et dolorum fuga. Et harum quidem rerum facilis est et expedita distinctio. Nam libero pore, cum soluta nobis est eligendi optio cumque nihil impedit quo minus id quod maxime placeat facere possimus...</p>
<div class="btn" style="left:100px;top:1366px;width:130px;height:42px;line-height:42px">Read More</div>
<div class="abs" style="left:655px;top:1028px;width:405px;height:390px;background:#cfcac4" role="img" aria-label="Warehouse photo"></div>
<div class="abs" style="left:757px;top:1148px;width:406px;height:268px;background:#d8d4cf" role="img" aria-label="Warehouse photo"></div>
<div class="abs" style="left:610px;top:1075px;width:404px;height:270px;background:linear-gradient(180deg,#3a3a3a,#6a7a3c 30%,#a8342c 55%,#4a4a3a 80%,#8a7a3a);box-shadow:0 6px 20px rgba(0,0,0,.3)" role="img" aria-label="Store shelves stocked with packaged goods"></div>
<div class="abs dots"><i style="background:var(--red)"></i><i></i><i></i></div>

<div class="abs band" style="top:1532px;height:554px"></div>
<h2 class="section-title center" style="top:1628px">Services</h2>
<div class="card" style="left:100px">
  <svg width="56" height="56" viewBox="0 0 56 56" fill="none" stroke="#ec1f27" stroke-width="2.5"><circle cx="28" cy="28" r="24"/><path d="M28 12v16l10 8"/></svg>
  <h3>INVENTORE VERITATIS</h3><p>At vero eos et accusamus et<br>iusto odio dignissimos ducimus</p><div class="btn">Read More</div></div>
<div class="card" style="left:352px">
  <svg width="56" height="56" viewBox="0 0 56 56" fill="none" stroke="#ec1f27" stroke-width="2.5"><circle cx="28" cy="28" r="24"/><path d="M28 13l4.5 9.5 10 1.2-7.4 6.9 2 10L28 35.6l-9.1 5 2-10-7.4-6.9 10-1.2z"/></svg>
  <h3>INVENTORE VERITATIS</h3><p>At vero eos et accusamus et<br>iusto odio dignissimos ducimus</p><div class="btn">Read More</div></div>
<div class="card" style="left:604px">
  <svg width="56" height="56" viewBox="0 0 56 56" fill="none" stroke="#ec1f27" stroke-width="2.5"><circle cx="28" cy="28" r="24"/><ellipse cx="28" cy="28" rx="10" ry="24"/><path d="M4 28h48M8 16h40M8 40h40"/></svg>
  <h3>INVENTORE VERITATIS</h3><p>At vero eos et accusamus et<br>iusto odio dignissimos ducimus</p><div class="btn">Read More</div></div>
<div class="card" style="left:856px">
  <svg width="56" height="56" viewBox="0 0 56 56" fill="none" stroke="#ec1f27" stroke-width="2.5"><rect x="6" y="26" width="10" height="24"/><path d="M16 28l10-18c4 0 6 3 5 8l-2 6h16c3 0 5 3 4 6l-4 16c-1 3-3 4-6 4H16"/></svg>
  <h3>INVENTORE VERITATIS</h3><p>At vero eos et accusamus et<br>iusto odio dignissimos ducimus</p><div class="btn">Read More</div></div>

<h2 class="section-title" style="left:100px;top:2184px">What We Do</h2>
<div class="abs" style="left:100px;top:2303px;width:512px;height:305px;background:linear-gradient(135deg,#3b3a3c,#c79a3e 45%,#e4b54a 60%,#6a4a32)" role="img" aria-label="Forklift moving pallets in a warehouse"></div>
<div class="abs wwd-list">
  <h4>Sit voluptatem accusantium doloremque</h4>
  <ul><li>Sed ut perspiciatis unde omnis iste</li><li>Natus error sit voluptatem accusantium</li><li>Doloremque laudantium</li><li>Totam rem aperiam</li><li>At vero eos et accusamus</li><li>Et iusto odio dignissimos</li><li>Natus error sit voluptatem accusantium</li><li>At vero eos et accusamus</li></ul>
</div>

<div class="abs band" style="top:2716px;height:711px"></div>
<h2 class="section-title center" style="top:2807px">Latest Blog</h2>
<div class="post" style="left:100px"><div class="ph" style="background:linear-gradient(180deg,#8fb7dc 50%,#6a7480 70%,#4a4f56)" role="img" aria-label="Container ship at port"></div>
  <p>Lorem ipsum dolor sit amet, consectetur adipiscing elit, sed do ...</p><div class="author"><i></i>OWEN MARSH</div><div class="btn">View Details</div></div>
<div class="post" style="left:445px"><div class="ph" style="background:linear-gradient(180deg,#b8473a,#2f5d8a 50%,#3d7a52 80%,#7a7a7a)" role="img" aria-label="Worker beside stacked containers"></div>
  <p>Lorem ipsum dolor sit amet, consectetur adipiscing elit, sed do ...</p><div class="author"><i></i>OWEN MARSH</div><div class="btn">View Details</div></div>
<div class="post" style="left:790px"><div class="ph" style="background:linear-gradient(135deg,#5a4a3a,#b88a4a 45%,#d9c070 60%,#6a5640)" role="img" aria-label="Two workers in a warehouse aisle"></div>
  <p>Lorem ipsum dolor sit amet, consectetur adipiscing elit, sed do ...</p><div class="author"><i></i>OWEN MARSH</div><div class="btn">View Details</div></div>

<footer class="abs footer"></footer>
<div class="abs foot-brand">HARBOR CRATE</div>
<div class="abs social"><i></i><i></i><i></i><i></i><i></i></div>
<div class="abs fcol contact" style="left:100px"><h5>Contact Us</h5>
  <ul>
    <li><svg width="12" height="16" viewBox="0 0 12 16" fill="#ddd" style="margin-top:5px"><path d="M6 0a6 6 0 016 6c0 4-6 10-6 10S0 10 0 6a6 6 0 016-6z"/><circle cx="6" cy="6" r="2" fill="#1c1b1c"/></svg><span>118 Dockside Way<br>Bayview FL 33100</span></li>
    <li><svg width="12" height="12" viewBox="0 0 24 24" fill="#ddd" style="margin-top:7px"><path d="M6.6 10.8a15 15 0 006.6 6.6l2.2-2.2c.3-.3.7-.4 1-.2 1.1.4 2.3.6 3.6.6.6 0 1 .4 1 1V20c0 .6-.4 1-1 1A17 17 0 013 4c0-.6.4-1 1-1h3.5c.6 0 1 .4 1 1 0 1.2.2 2.4.6 3.6.1.3 0 .7-.2 1z"/></svg>1-111-111-111</li>
    <li><svg width="13" height="10" viewBox="0 0 24 18" fill="#ddd" style="margin-top:8px"><path d="M0 0h24v18H0z"/></svg>info@harborcrate.com</li>
  </ul></div>
<div class="abs fcol" style="left:397px"><h5>Quick Links</h5><ul><li>Home</li><li>About Us</li><li>Services</li><li>What We Do</li></ul></div>
<div class="abs fcol" style="left:565px;top:3770px"><ul><li>Imports</li><li>Bolg</li><li>Contact Us</li></ul></div>
<div class="abs fcol" style="left:747px"><h5>Importance</h5><ul><li>Our Process</li><li>Products</li><li>Gallery</li><li>Sitemap</li></ul></div>
<div class="abs fcol" style="left:1004px"><h5>Legal</h5><ul><li>Faq</li><li>Privacy Policy</li><li>Terms &amp; Use</li><li>Delivery</li></ul></div>
<div class="abs bottombar">© 2018 Copyrights Harbor Crate Imports All Rights Reserved</div>

</body>
</html>
```